Hardcore nerd needs to stand out in a sea of dull Defence business cards

Wombarra Devices is a new Australian consulting engineering company that turns research and theory into practical systems. No evangelistic fluff, just mathematics and physics into electronic and optical circuits for consumer products, scientific research or Defence applications.

We already have a recognised logo (provided) which is often dark blue/black on a light background but we're open to other combinations. (Us engineers tend to have limited aesthetic imagination :)

Some of our recent products have included:
* Instrumentation for electrical testing,
* Radar jammers,
* GPS antenna design,
* Satellite tracking systems,
* High power lasers

We're open to both single and double-sided designs - happy to be convinced either way.

P.S. Another group is working on the web page, so - alas - our web site is currently of no use for images/ideas...

Target Market(s)

Engineering managers,
Scientists

Contact Information for Business Card

Dr Colin Harte
R&D Engineer

colin@wombarradevices.com.au
0427 563 710

PO Box XXX (to be confirmed)
Kelsby ACT 2917
Australia

Font styles to use
Serif
Sans Serif

Colors

Designer to choose colors to be used in the design.

Requirements
Must have
• My contact details!
• I've had many (great) "bold and plain" designs submitted already, so feel free to be artistically creative :)
• Happy to take advice re fonts/colours/printability etc.
Nice to have
• I'm not sure if "lists" are more at home on a CV than a business card, but representative services include:
• Applied electromagnetics
• RF and high speed electronics
• Signal and image processing
• Electro-optical and laser systems
• Concept-to-prototype design services
• If you're considering double sided cards, then often measuring/alignment grids/rulers feature on the back of similar cards.
• e.g. https://www.veltranoptics.example/newgrouppage9.cfm?objectgroup_id=4183
• https://www.veltranoptics.example/newgrouppage9.cfm?objectgroup_ID=4185
• ..or even a "Smith chart" (google will return lots)
• Generic images to represent a capability might work - googling images associated with keyword for each of these areas might help:
• - "passive radar", "phased array", "fdtd", "vircator"
• RF and high speed electronic design
• - "smith chart", "microstrip circuits", "dimensioned drawing", "electronic schematic"
• - "dft", "iir filter"
• - "optical cavity". "laser energy level diagram"
• Background/watermarked images outlines/wireframes/schematics would probably look OK.
Should not have
• If a list of projects/services is provided, it is important not to make the client feel that this is "all" the company can do. Engineering design is a creative discipline (like graphics :)
• Please, no stock "military" snaps like planes, missiles, etc!

```html
<!DOCTYPE html>
<html lang="en">
<head>
<meta charset="utf-8">
<title>Wombarra Devices – Business Card</title>
<link href="https://fonts.googleapis.com/css2?family=Roboto:wght@400;700&display=swap" rel="stylesheet">
<style>
  :root {
    --navy: #0a2a6b;
    --navy-deep: #00205e;
    --navy-top: #002b6f;
    --grey-text: #9a9a9a;
    --body-text: #3c3c3c;
    --rule: #7a7a7a;
    --stripe: #555555;
    --white: #ffffff;
    --backdrop: #e4e4e4;
  }
  * { margin: 0; padding: 0; box-sizing: border-box; }
  html, body {
    width: 1200px; height: 1200px; overflow: hidden;
    background: var(--backdrop);
    font-family: "Roboto", Arial, sans-serif;
  }
  .sheet {
    position: relative; width: 1200px; height: 1200px;
  }
  .card {
    position: absolute; left: 160px; width: 880px; height: 503px;
    overflow: hidden;
  }
  .card--front { top: 67px; background: var(--white); }
  .card--back {
    top: 630px;
    background: linear-gradient(180deg, var(--navy-top) 0%, var(--navy-deep) 100%);
  }

  /* Front */
  .brand {
    position: absolute; right: 45px; top: 52px;
    display: flex; align-items: center; gap: 14px;
    color: var(--navy); font-weight: 700;
  }
  .brand__dot {
    width: 118px; height: 118px; border-radius: 50%;
    background: var(--navy);
  }
  .brand__name { line-height: 1; }
  .brand__name span { display: block; }
  .brand__word-1 { font-size: 42px; letter-spacing: 1px; }
  .brand__word-2 { font-size: 23px; letter-spacing: 5.6px; margin-top: 4px; }

  .person { position: absolute; left: 44px; top: 282px; }
  .person__name { font-size: 29px; font-weight: 700; color: var(--navy); line-height: 1.1; }
  .person__role { font-size: 19px; color: var(--grey-text); margin-top: 4px; }

  .divider {
    position: absolute; left: 47px; right: 45px; top: 361px;
    border-top: 1px solid var(--rule);
  }
  .contact {
    position: absolute; top: 377px;
    font-size: 19px; line-height: 25px; color: var(--body-text);
  }
  .contact--left { left: 47px; }
  .contact--right { right: 45px; text-align: right; }

  .footer-band { position: absolute; left: 0; bottom: 0; width: 880px; height: 50px; }
  .footer-url {
    position: absolute; left: 577px; bottom: 13px;
    font-size: 19px; color: var(--white);
  }

  /* Back */
  .back-brand {
    position: absolute; left: 0; right: 0; top: 92px;
    display: flex; flex-direction: column; align-items: center; gap: 30px;
    color: var(--white); font-weight: 700;
  }
  .back-brand__dot { width: 150px; height: 150px; border-radius: 50%; background: var(--white); }
  .back-brand__name { font-size: 34px; letter-spacing: 3px; }
  .services {
    position: absolute; left: 0; right: 0; top: 394px;
    text-align: center; color: var(--white);
    font-size: 19.5px; line-height: 25px;
  }
  .services .sep { display: inline-block; width: 7px; height: 7px; border-radius: 50%; background: var(--white); vertical-align: middle; margin: 0 4px 3px; }
</style>
</head>
<body>
<main class="sheet">
  <section class="card card--front" aria-label="Business card front">
    <div class="brand">
      <div class="brand__dot"></div>
      <div class="brand__name">
        <span class="brand__word-1">WOMBARRA</span>
        <span class="brand__word-2">DEVICES</span>
      </div>
    </div>

    <div class="person">
      <div class="person__name">Dr Colin Harte</div>
      <div class="person__role">R&amp;D Engineer</div>
    </div>

    <div class="divider"></div>

    <div class="contact contact--left">
      <div>P. 0427 563 710</div>
      <div>colin@wombarradevices.com.au</div>
    </div>
    <div class="contact contact--right">
      <div>PO Box 318</div>
      <div>Kelsby ACT 2917, Australia</div>
    </div>

    <svg class="footer-band" viewBox="0 0 880 50" aria-hidden="true">
      <polygon points="0,21 525,21 515,34 0,34" fill="var(--stripe)"/>
      <polygon points="0,36 880,36 880,50 0,50" fill="var(--navy)"/>
      <polygon points="550,0 880,0 880,50 512,50" fill="var(--navy)"/>
      <line x1="550" y1="0" x2="514" y2="36" stroke="var(--white)" stroke-width="2"/>
    </svg>
    <div class="footer-url">wombarradevices.com.au</div>
  </section>

  <section class="card card--back" aria-label="Business card back">
    <div class="back-brand">
      <div class="back-brand__dot"></div>
      <div class="back-brand__name">WOMBARRA DEVICES</div>
    </div>
    <div class="services">
      <div>Applied electromagnetics<span class="sep"></span>RF &amp; high speed electronics</div>
      <div>Signal &amp; image processing<span class="sep"></span>Electro-optical &amp; laser systems</div>
      <div>Concept-to-prototype design services</div>
    </div>
  </section>
</main>
</body>
</html>
```